Create modern and sleek business card for luxury real estate company

We're a "boutique" real estate office looking for a design that gets across a highly modern luxury brand. Blacks and whites are probably the best colors unless we try a silver foil for the logo. I've attached a version of our current logo here. I'd like to swap out the current font on there with Gotham Light Regular.

I'm looking to have one side of the card have the logo with the space for our agents info on the other side.

Target Market(s)

Young professionals in a "luxury" headspace

Industry/Entity Type

Real estate

Contact Information for Business Card

A place for agent name, cell number, website. The slogan "Quietly Redefining Fine Homes".

Font styles to use
Other font styles liked:
• Gotham Regular

Colors

Designer to choose only greyscale colors for use in the design.

Requirements
Must have
• Matte black as the background color. Clean lines and use of contrast. A specific design aspect that will use silver foil.
Nice to have
• Up in the air on integrating a QR code
Should not have
• Any houses or other real estate related design (ex: a clip art house)

```html
<!DOCTYPE html>
<html lang="en">
<head>
<meta charset="UTF-8">
<title>Meridian Estates – Business Card</title>
<link href="https://fonts.googleapis.com/css2?family=Montserrat:wght@300;400&family=Oswald:wght@600&family=Open+Sans:wght@400&display=swap" rel="stylesheet">
<style>
  :root {
    --stage: #1a1a1a;
    --card: #2b2b2b;
    --card-edge: #232323;
    --silver: #e6e6e6;
    --silver-soft: #bdbdbd;
    --muted: #9a9a9a;
  }
  * { margin: 0; padding: 0; box-sizing: border-box; }
  html, body {
    width: 1200px; height: 900px; overflow: hidden;
    background: var(--stage);
  }
  .canvas {
    width: 1200px; height: 900px;
    display: flex; flex-direction: column;
    align-items: center; justify-content: center; gap: 50px;
  }
  .card {
    width: 700px; height: 400px;
    background: var(--card);
    border-radius: 28px;
    box-shadow: 0 0 0 1px var(--card-edge), 0 18px 40px rgba(0,0,0,.55);
    position: relative;
  }

  /* Brand side */
  .brand-side {
    display: flex; flex-direction: column; align-items: center; justify-content: center;
  }
  .brand-name {
    font-family: "Montserrat", sans-serif;
    font-weight: 300;
    font-size: 46px; line-height: 1.1;
    letter-spacing: 6px;
    color: var(--silver);
    text-transform: uppercase;
    white-space: nowrap;
  }
  .brand-rule {
    width: 460px; height: 1px; background: var(--silver-soft);
    margin: 24px 0 18px;
  }
  .slogan {
    font-family: "Montserrat", sans-serif;
    font-weight: 400; font-size: 17px;
    letter-spacing: 3px; color: var(--silver);
    text-transform: uppercase;
    white-space: nowrap;
  }

  /* Agent side */
  .agent-side {
    display: flex; align-items: center; justify-content: center; gap: 34px;
  }
  .agent-id { text-align: right; }
  .agent-name {
    font-family: "Oswald", sans-serif; font-weight: 600;
    font-size: 40px; letter-spacing: 1px;
    color: var(--silver); text-transform: uppercase; line-height: 1.1;
    white-space: nowrap;
  }
  .agent-role {
    font-family: "Open Sans", sans-serif; font-size: 16px;
    color: var(--silver-soft); margin-top: 4px;
  }
  .divider { width: 1px; height: 120px; background: var(--muted); }
  .contact-list { list-style: none; display: flex; flex-direction: column; gap: 10px; }
  .contact-item {
    display: flex; align-items: center; gap: 10px;
    font-family: "Open Sans", sans-serif; font-size: 19px;
    color: var(--silver); white-space: nowrap;
  }
  .contact-icon { width: 16px; height: 16px; flex: none; }
</style>
</head>
<body>
<main class="canvas">
  <section class="card brand-side">
    <div class="brand-name">Meridian Estates</div>
    <div class="brand-rule"></div>
    <p class="slogan">Quietly Redefining Fine Homes</p>
  </section>

  <section class="card agent-side">
    <div class="agent-id">
      <h1 class="agent-name">Daniel Hayes</h1>
      <p class="agent-role">Director</p>
    </div>
    <div class="divider"></div>
    <ul class="contact-list">
      <li class="contact-item">
        <svg class="contact-icon" viewBox="0 0 16 16" aria-hidden="true"><path d="M4 1.5l2.2 3-1.4 1.6c.8 1.8 2.3 3.3 4.1 4.1l1.6-1.4 3 2.2-1 2.5C7.5 13.6 2.4 8.5 1.5 3.5z" fill="#e6e6e6"/></svg>
        555.201.7390
      </li>
      <li class="contact-item">
        <svg class="contact-icon" viewBox="0 0 16 16" aria-hidden="true"><rect x="1.5" y="3.5" width="13" height="9" fill="none" stroke="#e6e6e6" stroke-width="1.4"/><path d="M1.5 3.5L8 9l6.5-5.5" fill="none" stroke="#e6e6e6" stroke-width="1.4"/></svg>
        hello@meridianestates.com
      </li>
      <li class="contact-item">
        <svg class="contact-icon" viewBox="0 0 16 16" aria-hidden="true"><circle cx="8" cy="8" r="6.5" fill="none" stroke="#e6e6e6" stroke-width="1.3"/><ellipse cx="8" cy="8" rx="2.8" ry="6.5" fill="none" stroke="#e6e6e6" stroke-width="1.1"/><path d="M1.5 8h13" stroke="#e6e6e6" stroke-width="1.1"/></svg>
        www.meridianestates.com
      </li>
    </ul>
  </section>
</main>
</body>
</html>
```